Business card for a Exhibition booth fabrication company

Hi. My company would like to change our corporate name card. We are an events and Exhibition stand builder company. We would like our corporate name card to resonate what we do. I need someone to create something unique that relates to the industry that I am in. The graphic designer should be creative to incorporate the elements of my industry and try to blend in well in the design of the card. Our aim is to ensure that we are unique and our card can look different from our competitors.
Updates

Target Market(s)

Marketing and events manager from all companies

Contact Information for Business Card

The business card should have the following details:
Name
Job Title
Email
Website

Colors

Designer to choose colors to be used in the design.

Requirements
Must have
• The card must be look something that is relevant to the service that I am providing. My website is: www.velmora-buildworks.com
• You can see my website to get more information on what service that I am doing
Nice to have
• On the back of my card, I would like to have a globe image with the incorporation of my company logo. This is to indicate that my services can be done in any part of the world.

```html
<!DOCTYPE html>
<html lang="en">
<head>
<meta charset="utf-8">
<title>Velmora Buildworks – Business Card</title>
<link rel="stylesheet" href="https://fonts.googleapis.com/css2?family=Open+Sans:wght@400;600&family=Arimo:wght@400;700&display=swap">
<style>
  :root {
    --brand-red: #ec1c24;
    --ink: #4a4a4a;
    --ink-soft: #5c5c5c;
    --paper: #ffffff;
    --backdrop: #d6d7d9;
    --map-grey: #d9d9d9;
    --map-grey-light: #ededed;
  }
  * { margin: 0; padding: 0; box-sizing: border-box; }
  html, body {
    width: 1200px; height: 1118px; overflow: hidden;
    background: var(--backdrop);
  }
  .canvas { position: relative; width: 1200px; height: 1118px; }

  .card {
    position: absolute;
    width: 756px; height: 430px;
    background: var(--paper);
    border-radius: 34px;
    overflow: hidden;
    box-shadow: 0 4px 14px rgba(0,0,0,0.12);
  }
  .card--front { left: 257px; top: 112px; }
  .card--back  { left: 269px; top: 591px; height: 428px; }

  .wave { position: absolute; left: 0; top: 0; width: 756px; height: 430px; }

  .company-name {
    position: absolute; left: 66px; top: 112px;
    font-family: "Open Sans", sans-serif; font-weight: 600;
    font-size: 32px; letter-spacing: 2px; line-height: 40px;
    color: var(--brand-red);
  }

  .contact-list { position: absolute; left: 64px; top: 181px; list-style: none; }
  .contact-item {
    display: flex; align-items: center; gap: 10px;
    height: 34px;
    font-family: "Open Sans", sans-serif; font-size: 19px; color: var(--ink);
  }
  .contact-icon { width: 18px; height: 18px; flex: none; }

  .address {
    position: absolute; left: 66px; top: 295px;
    font-family: "Open Sans", sans-serif; font-size: 19px; line-height: 26px;
    color: var(--ink-soft);
  }

  .holder {
    position: absolute; right: 34px; top: 356px;
    text-align: center; color: var(--paper); font-family: "Arimo", sans-serif;
  }
  .holder-name { font-weight: 700; font-size: 24px; line-height: 28px; letter-spacing: 0.5px; }
  .holder-title { font-size: 19px; line-height: 24px; margin-top: 2px; letter-spacing: 0.5px; }

  .world-map {
    position: absolute; left: 45px; top: 53px; width: 675px; height: 282px;
    border-radius: 50% 50% 8% 8% / 60% 60% 10% 10%;
    background: radial-gradient(ellipse at 50% 55%, var(--map-grey) 0%, var(--map-grey-light) 70%, rgba(255,255,255,0) 100%);
  }
  .map-shadow {
    position: absolute; left: 80px; top: 340px; width: 600px; height: 34px;
    border-radius: 50%;
    background: radial-gradient(ellipse, rgba(0,0,0,0.12) 0%, rgba(0,0,0,0) 70%);
  }
  .back-name {
    position: absolute; left: 0; right: 0; top: 248px; text-align: center;
    font-family: "Open Sans", sans-serif; font-weight: 600;
    font-size: 36px; letter-spacing: 2px; color: var(--brand-red);
  }
  .back-website {
    position: absolute; left: 0; right: 0; top: 388px; text-align: center;
    font-family: "Open Sans", sans-serif; font-size: 21px; letter-spacing: 4px;
    color: var(--ink);
  }
</style>
</head>
<body>
<main class="canvas">

  <section class="card card--front" aria-label="Business card front">
    <svg class="wave" viewBox="0 0 756 430" aria-hidden="true">
      <path d="M0,262 C10,345 60,385 150,392 C300,402 450,330 560,298 C640,276 720,262 756,262 L756,430 L0,430 Z" fill="var(--brand-red)"/>
      <path d="M30,380 C200,425 380,330 756,278 L756,290 C380,345 200,437 30,380 Z" fill="var(--paper)"/>
    </svg>

    <div class="company-name">VELMORA BUILDWORKS</div>

    <ul class="contact-list">
      <li class="contact-item">
        <svg class="contact-icon" viewBox="0 0 24 24" aria-hidden="true"><path fill="var(--brand-red)" d="M6.6 10.8a15.1 15.1 0 0 0 6.6 6.6l2.2-2.2a1 1 0 0 1 1-.25 11.4 11.4 0 0 0 3.6.57 1 1 0 0 1 1 1V20a1 1 0 0 1-1 1A17 17 0 0 1 3 4a1 1 0 0 1 1-1h3.5a1 1 0 0 1 1 1c0 1.25.2 2.45.57 3.57a1 1 0 0 1-.25 1z"/></svg>
        <span>012-555-0147</span>
      </li>
      <li class="contact-item">
        <svg class="contact-icon" viewBox="0 0 24 24" aria-hidden="true"><rect x="2" y="5" width="20" height="14" fill="var(--brand-red)"/><path d="M2 5l10 8 10-8" fill="none" stroke="#fff" stroke-width="1.6"/></svg>
        <span>info@velmorabuildworks.com</span>
      </li>
      <li class="contact-item">
        <svg class="contact-icon" viewBox="0 0 24 24" aria-hidden="true"><g fill="none" stroke="var(--brand-red)" stroke-width="1.8"><circle cx="12" cy="12" r="10"/><ellipse cx="12" cy="12" rx="4.5" ry="10"/><path d="M2 12h20M4 7h16M4 17h16"/></g></svg>
        <span>www.velmora-buildworks.com</span>
      </li>
    </ul>

    <p class="address">Street Name, City Name<br>Zipcode - 01234</p>

    <div class="holder">
      <div class="holder-name">DARREN HOLLOWAY</div>
      <div class="holder-title">PRESIDENT</div>
    </div>
  </section>

  <section class="card card--back" aria-label="Business card back">
    <div class="world-map" role="img" aria-label="Grey world map curving over the card like a globe"></div>
    <div class="map-shadow"></div>
    <div class="back-name">VELMORA BUILDWORKS</div>
    <div class="back-website">www.velmora-buildworks.com</div>
  </section>

</main>
</body>
</html>
```